Veldmark Supplies Business Card

Professional business card that stand out to our potential customers. Front and back with clean modern design

Industry/Entity Type

Oil and gas

Contact Information for Business Card

Name, address, website , office phone and cell number

Requirements
Must have
• Editable files for each employee

```html
<!DOCTYPE html>
<html lang="en">
<head>
<meta charset="utf-8">
<title>Veldmark Supplies Business Card</title>
<link href="https://fonts.googleapis.com/css2?family=Roboto:wght@400;500;700&display=swap" rel="stylesheet">
<style>
  :root {
    --bg: #e6e7e9;
    --card: #ffffff;
    --red: #e11d25;
    --blue: #22a9d6;
    --ink: #2b2b2b;
    --muted: #4a4a4a;
  }
  * { box-sizing: border-box; margin: 0; padding: 0; }
  html, body { width: 1200px; height: 852px; overflow: hidden; }
  body {
    background: var(--bg);
    font-family: "Roboto", Arial, sans-serif;
    position: relative;
  }
  .card {
    position: absolute;
    top: 283px;
    width: 500px;
    height: 286px;
    background: var(--card);
    border-radius: 22px;
    overflow: hidden;
    box-shadow: 0 6px 18px rgba(0,0,0,0.12);
  }
  .card-front { left: 80px; }
  .card-back { left: 620px; }

  .front-brand {
    position: absolute;
    left: 0; right: 0; top: 128px;
    text-align: center;
    font-size: 28px;
    font-weight: 700;
    letter-spacing: 1px;
    text-transform: uppercase;
    color: var(--red);
  }
  .front-strip {
    position: absolute;
    left: 0; right: 0; bottom: 0;
    height: 7px;
    display: flex;
  }
  .front-strip .strip-red { flex: 1; background: var(--red); }
  .front-strip .strip-blue { flex: 1; background: var(--blue); }

  .back-shape { position: absolute; inset: 0; }
  .back-brand {
    position: absolute;
    left: 34px; top: 168px;
    width: 190px;
    font-size: 22px;
    font-weight: 700;
    line-height: 1.15;
    text-transform: uppercase;
    color: #ffffff;
  }
  .contact {
    position: absolute;
    left: 300px; top: 40px;
    color: var(--muted);
    font-size: 12px;
    line-height: 1.35;
  }
  .contact-name {
    font-size: 19px;
    font-weight: 500;
    color: var(--blue);
    line-height: 1.1;
  }
  .contact-title { margin-bottom: 16px; }
  .contact-address { margin-bottom: 8px; }
  .contact-line { display: flex; align-items: center; gap: 6px; }
  .contact-line svg { width: 10px; height: 10px; flex: none; }
</style>
</head>
<body>

  <section class="card card-front" aria-label="Card front">
    <div class="front-brand">Veldmark Supplies</div>
    <div class="front-strip">
      <span class="strip-red"></span>
      <span class="strip-blue"></span>
    </div>
  </section>

  <section class="card card-back" aria-label="Card back">
    <svg class="back-shape" viewBox="0 0 500 286" aria-hidden="true">
      <path d="M0 70 C 170 40, 260 120, 292 286 L0 286 Z" fill="var(--blue)"/>
      <path d="M0 78 C 160 50, 245 125, 276 286 L0 286 Z" fill="var(--red)"/>
    </svg>
    <div class="back-brand">Veldmark Supplies</div>

    <div class="contact">
      <div class="contact-name">Jordan Vale</div>
      <div class="contact-title">Managing Director</div>
      <div class="contact-address">418 Harlow Ridge Suite 5<br>Midvale, Tx 79702</div>
      <div class="contact-line">
        <svg viewBox="0 0 10 10" aria-hidden="true"><path d="M1 2.5 Q5 0 9 2.5 L8 4 L6.5 3.5 L3.5 3.5 L2 4 Z M2.5 5 H7.5 L8.5 9 H1.5 Z" fill="var(--red)"/></svg>
        <span>(555)014-2270</span>
      </div>
      <div class="contact-line">
        <svg viewBox="0 0 10 10" aria-hidden="true"><rect x="0.5" y="2" width="9" height="6.5" fill="var(--red)"/><path d="M0.5 2 L5 6 L9.5 2" stroke="#fff" stroke-width="1" fill="none"/></svg>
        <span>sales@veldmarksupplies.com</span>
      </div>
      <div class="contact-line">
        <svg viewBox="0 0 10 10" aria-hidden="true"><circle cx="5" cy="5" r="4.5" fill="var(--red)"/><path d="M0.5 5 H9.5 M5 0.5 Q2 5 5 9.5 M5 0.5 Q8 5 5 9.5" stroke="#fff" stroke-width="0.8" fill="none"/></svg>
        <span>www.veldmarksupplies.com</span>
      </div>
    </div>
  </section>

</body>
</html>
```